Business Card Design for BrightvaleMedia.com

--I need a business card design for my company BrightvaleMedia.com

I have attached my logo...I want the brightvale media logo on the front of the business card, and then I want The Quillstone Chief on the back of it with my information.

I would like to see a light colored background as well as a dark colored background

FRONT:
BRIGHTVALE MEDIA LOGO
248 N. Larkmoor
3rd Floor
San Diego CA 92173
www.BrightvaleMedia.com

Advanced Website & App Development
Websites, Apps, Online Voucher Systems

Leading Edge Marketing Services
SMS, VB, SMM, SEM,

BACK:
QUILLSTONE CHIEF LOGO
Dorian Pelletta
The Quillstone Chief
Call Or Text: 619-555-0148
Dorian@QuillstoneChief.example
www.QuillstoneChief.example

Target Market(s)

small business owners

Industry/Entity Type

Business Consultant

Contact Information for Business Card

FRONT:
BRIGHTVALE MEDIA LOGO
248 N. Larkmoor
3rd Floor
San Diego CA 92173
www.BrightvaleMedia.com

SMS, VB, SMM, SEM,

BACK:
QUILLSTONE CHIEF LOGO
Dorian Pelletta
The Quillstone Chief
Dorian@QuillstoneChief.example
www.QuillstoneChief.example

Requirements
Must have
• add this quote on it somewhere, anywhere,preferrably on back
• "The Fastest Way To Success Is To Take Action”
• — Dorian Pelletta, Quillstone Chief
Nice to have
• open
Should not have
• red

```html
<!DOCTYPE html>
<html lang="en">
<head>
<meta charset="utf-8">
<title>Brightvale Media Business Cards</title>
<link rel="stylesheet" href="https://fonts.googleapis.com/css2?family=Source+Sans+3:ital,wght@0,400;0,600;1,400&display=swap">
<style>
  :root {
    --stage: #3b3b3b;
    --card-white: #ffffff;
    --brand-blue: #0a72aa;
    --band-blue: #0872a8;
    --rule-grey: #9a9a9a;
    --text-grey: #4a4a4a;
    --text-muted: #6a6a6a;
    --text-light: #ffffff;
  }
  * { margin: 0; padding: 0; box-sizing: border-box; }
  html, body {
    width: 1105px;
    height: 1200px;
    overflow: hidden;
    background: var(--stage);
    font-family: "Source Sans 3", sans-serif;
  }
  .canvas { position: relative; width: 1105px; height: 1200px; }

  .card {
    position: absolute;
    left: 196px;
    width: 720px;
    height: 411px;
    background: var(--card-white);
    box-shadow: 0 3px 10px rgba(0,0,0,0.55);
    overflow: hidden;
  }
  .card--front { top: 146px; }
  .card--back { top: 602px; }

  .card__rule {
    position: absolute;
    left: 0; right: 0;
    height: 2px;
    background: var(--rule-grey);
  }
  .card__band {
    position: absolute;
    left: 0; right: 0; bottom: 0;
    background: var(--band-blue);
    color: var(--text-light);
  }
  .card--front .card__rule { top: 237px; }
  .card--front .card__band { top: 242px; }
  .card--back .card__rule { top: 229px; }
  .card--back .card__band { top: 235px; }

  .wordmark {
    position: absolute;
    left: 0; right: 0;
    text-align: center;
    color: var(--brand-blue);
    font-weight: 600;
    line-height: 1;
  }
  .wordmark__main { display: block; letter-spacing: 3px; }
  .wordmark__sub { display: block; letter-spacing: 8px; }
  .card--front .wordmark { top: 62px; }
  .card--front .wordmark__main { font-size: 46px; }
  .card--front .wordmark__sub { font-size: 18px; margin-top: 6px; }
  .card--back .wordmark { top: 58px; }
  .card--back .wordmark__main { font-size: 56px; }
  .card--back .wordmark__sub { font-size: 24px; margin-top: 6px; }

  .address {
    position: absolute;
    top: 156px; left: 0; right: 0;
    text-align: center;
    font-size: 19px;
    line-height: 26px;
    color: var(--text-grey);
  }
  .address__url { color: var(--brand-blue); font-weight: 600; }

  .quote {
    position: absolute;
    top: 170px; left: 0; right: 0;
    text-align: center;
    color: var(--text-muted);
    line-height: 22px;
  }
  .quote__text { font-size: 17px; font-style: italic; }
  .quote__author { display: block; font-size: 14px; }

  .services {
    text-align: center;
    font-size: 19px;
    line-height: 26px;
    padding-top: 24px;
  }
  .services__group + .services__group { margin-top: 14px; }

  .identity {
    position: absolute;
    top: 64px;
    right: 426px;
    text-align: right;
  }
  .identity__name { font-size: 26px; font-weight: 600; line-height: 32px; }
  .identity__title { font-size: 19px; line-height: 26px; }

  .divider {
    position: absolute;
    left: 318px; top: 44px;
    width: 1px; height: 82px;
    background: var(--text-light);
    opacity: 0.8;
  }

  .contact {
    position: absolute;
    left: 351px; top: 46px;
    list-style: none;
    font-size: 19px;
    line-height: 27.5px;
  }
  .contact__item { display: flex; align-items: center; }
  .contact__icon { width: 16px; height: 16px; margin-right: 9px; flex: none; }
</style>
</head>
<body>
<main class="canvas">

  <section class="card card--front" aria-label="Card front">
    <div class="wordmark">
      <span class="wordmark__main">BRIGHTVALE</span>
      <span class="wordmark__sub">MEDIA</span>
    </div>
    <p class="address">
      248 N. Larkmoor, 3rd Floor, San Diego CA 92173<br>
      <span class="address__url">www.BrightvaleMedia.com</span>
    </p>
    <div class="card__rule"></div>
    <div class="card__band">
      <div class="services">
        <p class="services__group">Advanced Website &amp; App Development<br>Websites • Apps • Online Voucher Systems</p>
        <p class="services__group">Leading Edge Marketing Services<br>SMS • VB • SMM • SEM</p>
      </div>
    </div>
  </section>

  <section class="card card--back" aria-label="Card back">
    <div class="wordmark">
      <span class="wordmark__main">QUILLSTONE</span>
      <span class="wordmark__sub">CHIEF</span>
    </div>
    <blockquote class="quote">
      <span class="quote__text">“The Fastest Way To Success Is To Take Action”</span>
      <span class="quote__author">— Dorian Pelletta, Quillstone Chief</span>
    </blockquote>
    <div class="card__rule"></div>
    <div class="card__band">
      <div class="identity">
        <p class="identity__name">Dorian Pelletta</p>
        <p class="identity__title">The Quillstone Chief</p>
      </div>
      <div class="divider"></div>
      <ul class="contact">
        <li class="contact__item">
          <svg class="contact__icon" viewBox="0 0 16 16" aria-hidden="true">
            <path fill="#fff" d="M3.2 1.2l2.4 2.6-1.3 1.8c.9 2.1 2.7 3.9 4.9 4.9l1.8-1.3 2.6 2.4-1.3 2.4C6.6 13.7 2.3 9.4 0.8 3.5z"/>
          </svg>
          619-555-0148
        </li>
        <li class="contact__item">
          <svg class="contact__icon" viewBox="0 0 16 16" aria-hidden="true">
            <rect x="1" y="3" width="14" height="10" fill="#fff"/>
            <path d="M1 3l7 5.5L15 3" fill="none" stroke="#0872a8" stroke-width="1.4"/>
          </svg>
          Dorian@QuillstoneChief.example
        </li>
        <li class="contact__item">
          <svg class="contact__icon" viewBox="0 0 16 16" aria-hidden="true">
            <circle cx="8" cy="8" r="7" fill="#fff"/>
            <path d="M4 5.5c1.5.5 2 1.8 1.2 3.2M10 3.5c-.5 1.5.5 2.5 2 2.5M9 10.5c1 .3 1.5 1.5 1 2.8" fill="none" stroke="#0872a8" stroke-width="1.5"/>
          </svg>
          www.QuillstoneChief.example
        </li>
      </ul>
    </div>
  </section>

</main>
</body>
</html>
```